Business Card for a Jewellery Brand

Business card for an upscale jewellery brand. Attached is the brand logo and icon and color board. I am looking for two card versions: one for the founder and one is generic. The card should be elegant and convey upscale and premium feel. I am open to both square and rectangle card shapes.

Industry/Entity Type

Jewelry

Contact Information for Business Card

Two cards: (1) Sunela Parvaniya (Founder) (2) General
(1) Sunela Parvaniya card should have Name: Sunela Parvaniya, Title: Founder Email id: sunela@quiremo.com.au. Phone no: +61452913307
(2) Generic card should have Email id: info@quiremo.com.au. Phone no: +61436207518

Requirements
Must have
• Workmark
• ICON
• Phone no
• Email ID
• ABN: 58219740312 (Note: ABN is Business number in Australia)
• Website: www.quiremo.com.au
• Instagram: quiremo_jewellery
• Facebook: @quiremojewellery
Nice to have
• Tagline

```html
<!DOCTYPE html>
<html lang="en">
<head>
<meta charset="utf-8">
<title>Quiremo Business Cards</title>
<link href="https://fonts.googleapis.com/css2?family=Jost:wght@400;500&display=swap" rel="stylesheet">
<style>
  :root {
    --backdrop: #1e1e1e;
    --card: #ffffff;
    --rose: #e09a94;
    --ink: #3a3a3a;
    --muted: #555555;
  }
  * { margin: 0; padding: 0; box-sizing: border-box; }
  html, body {
    width: 1200px; height: 929px; overflow: hidden;
    background: var(--backdrop);
    font-family: "Jost", "Futura", sans-serif;
  }
  .stage { position: relative; width: 1200px; height: 929px; }
  .card {
    position: absolute;
    width: 520px; height: 316px;
    background: var(--card);
  }
  .card--front { left: 110px; top: 110px; }
  .card--back { left: 570px; top: 500px; }

  .wordmark {
    display: flex; align-items: center; gap: 14px;
    color: var(--rose); font-weight: 400; letter-spacing: 0.18em;
  }
  .wordmark__dot {
    width: 16px; height: 16px; border-radius: 50%; background: var(--rose);
  }
  .card--front .wordmark {
    position: absolute; left: 0; right: 0; top: 0; bottom: 0;
    justify-content: center; font-size: 44px;
  }
  .card--back .wordmark {
    position: absolute; left: 34px; top: 140px; font-size: 28px; gap: 10px;
  }
  .card--back .wordmark__dot { width: 12px; height: 12px; }

  .divider {
    position: absolute; left: 250px; top: 88px;
    width: 1.5px; height: 170px; background: var(--rose);
  }
  .abn {
    position: absolute; right: 26px; top: 22px;
    font-size: 13px; color: var(--ink); letter-spacing: 0.04em;
  }
  .abn__label { color: var(--rose); }
  .details { position: absolute; left: 272px; top: 88px; }
  .person__name {
    color: var(--rose); font-size: 17px; font-weight: 400;
    letter-spacing: 0.05em; text-transform: uppercase;
  }
  .person__role {
    color: var(--ink); font-size: 12px; font-weight: 500;
    letter-spacing: 0.04em; margin-bottom: 14px;
  }
  .contacts { list-style: none; }
  .contacts li {
    display: flex; align-items: center; gap: 10px;
    font-size: 13px; color: var(--muted); letter-spacing: 0.03em;
    line-height: 22px;
  }
  .contacts svg { width: 12px; height: 12px; flex: none; }
  .plain-mark { width: 11px; height: 11px; background: var(--rose); flex: none; }
  .plain-mark--round { border-radius: 50%; }
</style>
</head>
<body>
<main class="stage">
  <section class="card card--front" aria-label="Card front">
    <div class="wordmark"><span class="wordmark__dot"></span>QUIREMO</div>
  </section>

  <section class="card card--back" aria-label="Card back">
    <div class="abn"><span class="abn__label">ABN:</span> 58219740312</div>
    <div class="wordmark"><span class="wordmark__dot"></span>QUIREMO</div>
    <div class="divider"></div>
    <div class="details">
      <h1 class="person__name">Sunela Parvaniya</h1>
      <p class="person__role">FOUNDER</p>
      <ul class="contacts">
        <li>
          <svg viewBox="0 0 12 12"><rect x="2.5" y="0.5" width="7" height="11" rx="1.2" fill="none" stroke="var(--rose)"/></svg>
          +61452913307
        </li>
        <li>
          <svg viewBox="0 0 12 12"><circle cx="6" cy="6" r="5" fill="none" stroke="var(--rose)"/><path d="M1 6h10M6 1c-2.5 3-2.5 7 0 10M6 1c2.5 3 2.5 7 0 10" fill="none" stroke="var(--rose)" stroke-width="0.8"/></svg>
          www.quiremo.com.au
        </li>
        <li>
          <svg viewBox="0 0 12 12"><rect x="0.5" y="2" width="11" height="8" fill="var(--rose)"/><path d="M0.5 2l5.5 4.5L11.5 2" fill="none" stroke="#fff" stroke-width="1"/></svg>
          sunela@quiremo.com.au
        </li>
        <li><span class="plain-mark"></span>@quiremojewellery</li>
        <li><span class="plain-mark plain-mark--round"></span>quiremo_jewellery</li>
      </ul>
    </div>
  </section>
</main>
</body>
</html>
```